Tall Fern Roofing Business Card

Need a business card with the logo that was designed here

Contact Information for Business Card

Name, Title, Phone, Email, Website, Company name

```html
<!DOCTYPE html>
<html lang="en">
<head>
<meta charset="utf-8">
<title>Tall Fern Roofing – Business Card</title>
<link rel="stylesheet" href="https://fonts.googleapis.com/css2?family=Poppins:wght@400;600;700&family=Great+Vibes&display=swap">
<style>
  :root {
    --backdrop: #2b2b2d;
    --card: #1b1c1e;
    --card-edge: #232427;
    --brand-blue: #1f7fd1;
    --silver: #b4b6b9;
    --grey-text: #a9abae;
    --rule: #77797c;
    --pattern-dark: #141517;
    --pattern-light: #2c2d31;
  }
  * { box-sizing: border-box; margin: 0; padding: 0; }
  html, body { width: 1200px; height: 1108px; overflow: hidden; }
  body {
    background: var(--backdrop);
    font-family: "Poppins", sans-serif;
    position: relative;
  }
  .card {
    position: absolute;
    top: 234px;
    width: 400px;
    height: 640px;
    background: var(--card);
    border: 1px solid var(--card-edge);
    border-radius: 24px;
    overflow: hidden;
    box-shadow: 0 18px 40px rgba(0,0,0,.45);
  }
  .card--front { left: 150px; }
  .card--back { left: 650px; }

  /* Front */
  .company-mark {
    position: absolute;
    top: 170px;
    left: 0; right: 0;
    display: flex;
    align-items: center;
    justify-content: center;
    gap: 12px;
  }
  .company-mark__square {
    width: 18px; height: 18px;
    background: var(--brand-blue);
  }
  .company-mark__name {
    font-weight: 600;
    font-size: 30px;
    color: var(--brand-blue);
    letter-spacing: .5px;
  }
  .person {
    position: absolute;
    top: 390px;
    left: 0; right: 0;
    text-align: center;
  }
  .person__name { line-height: 1; }
  .person__first {
    font-family: "Great Vibes", cursive;
    font-size: 44px;
    color: var(--brand-blue);
  }
  .person__last {
    font-weight: 700;
    font-size: 26px;
    color: var(--silver);
    margin-left: 6px;
  }
  .person__title {
    margin-top: 6px;
    font-size: 16px;
    color: var(--brand-blue);
    letter-spacing: .5px;
  }
  .contact-icons {
    position: absolute;
    top: 488px;
    left: 40px; right: 40px;
    display: flex;
    align-items: center;
    gap: 10px;
  }
  .contact-icons__rule { flex: 1; height: 1px; background: var(--rule); }
  .contact-icons__item {
    width: 28px; height: 28px;
    background: var(--brand-blue);
    border-radius: 4px;
    display: flex; align-items: center; justify-content: center;
  }
  .contact-list {
    position: absolute;
    top: 528px;
    left: 0; right: 0;
    list-style: none;
    text-align: center;
    font-size: 17px;
    line-height: 1.45;
    color: var(--grey-text);
  }

  /* Back */
  .back-pattern {
    position: absolute; inset: 0;
    background: linear-gradient(135deg, var(--pattern-light) 0%, var(--pattern-dark) 55%, var(--pattern-light) 100%);
  }
  .back-mark {
    position: absolute;
    top: 410px;
    left: 0; right: 0;
    display: flex;
    align-items: center;
    justify-content: center;
    gap: 8px;
  }
  .back-mark__square { width: 10px; height: 10px; background: var(--brand-blue); }
  .back-mark__name {
    font-weight: 600;
    font-size: 18px;
    color: var(--brand-blue);
  }
</style>
</head>
<body>
  <section class="card card--front" aria-label="Card front">
    <div class="company-mark">
      <span class="company-mark__square"></span>
      <span class="company-mark__name">Tall Fern Roofing</span>
    </div>

    <div class="person">
      <p class="person__name"><span class="person__first">Marcus</span><span class="person__last">REED</span></p>
      <p class="person__title">MANAGING DIRECTOR</p>
    </div>

    <div class="contact-icons">
      <span class="contact-icons__rule"></span>
      <span class="contact-icons__item" aria-label="Phone">
        <svg width="16" height="16" viewBox="0 0 24 24"><path fill="#1b1c1e" d="M6.6 10.8a15 15 0 0 0 6.6 6.6l2.2-2.2a1 1 0 0 1 1-.25 11.4 11.4 0 0 0 3.6.57 1 1 0 0 1 1 1V20a1 1 0 0 1-1 1A17 17 0 0 1 3 4a1 1 0 0 1 1-1h3.5a1 1 0 0 1 1 1c0 1.25.2 2.45.57 3.57a1 1 0 0 1-.25 1z"/></svg>
      </span>
      <span class="contact-icons__item" aria-label="Email">
        <svg width="16" height="16" viewBox="0 0 24 24"><rect x="3" y="6" width="18" height="12" fill="none" stroke="#1b1c1e" stroke-width="2"/><path d="M3 6l9 7 9-7" fill="none" stroke="#1b1c1e" stroke-width="2"/></svg>
      </span>
      <span class="contact-icons__item" aria-label="Website">
        <svg width="16" height="16" viewBox="0 0 24 24"><circle cx="12" cy="12" r="9" fill="none" stroke="#1b1c1e" stroke-width="2"/><path d="M3 12h18M12 3c3 3 3 15 0 18M12 3c-3 3-3 15 0 18" fill="none" stroke="#1b1c1e" stroke-width="1.6"/></svg>
      </span>
      <span class="contact-icons__rule"></span>
    </div>

    <ul class="contact-list">
      <li>044-987 210 654</li>
      <li>hello@tallfernroof.com</li>
      <li>www.tallfernroof.com</li>
    </ul>
  </section>

  <section class="card card--back" aria-label="Card back">
    <div class="back-pattern" role="img" aria-label="Repeating tonal pattern of the company name in spot gloss"></div>
    <div class="back-mark">
      <span class="back-mark__square"></span>
      <span class="back-mark__name">Tall Fern Roofing</span>
    </div>
  </section>
</body>
</html>
```